Modern and Sleek Non-Fiction Book Cover Design

Seeking a talented graphic designer to create a modern and sleek cover and back page for a book to be published on Folionet . The design should be visually appealing and align with the book's theme, using bright colors to make it stand out. The title is "A Studio Ledger Field Manual" with "The" in a smaller font, and the tagline "Intake as a Competitive Advantage" should be included. The book is targeted at an audience interested in immigration and family law firms. So I would like it on the cover as well. The hex numbers for the colors are 00aeeef, fcb034, and 336a89. The cover should feature the author's photo prominently.
Deliverables
-Design a modern front cover for the book
-Design a sleek back page for the book
-Ensure designs meet Folionet publishing requirements 8x5 paperback
Let's not use the side image, it doesn't seem to fit like I thought it might.

```html
<!DOCTYPE html>
<html lang="en">
<head>
<meta charset="utf-8">
<title>A Studio Ledger Field Manual – Cover Wrap</title>
<link rel="stylesheet" href="https://fonts.googleapis.com/css2?family=Lexend:wght@300;400;700&display=swap">
<style>
  :root {
    --stage: #555555;
    --paper-top: #f1ebe1;
    --paper-bottom: #e6d9c4;
    --title-blue: #2e6f94;
    --ink: #1d1d1d;
    --rule-blue: #4a9cc9;
    --photo-blue: #1f7fc0;
    --jacket-brown: #7a3f2a;
    --skyline: #d9b78f;
    --barcode-box: #f4f4f4;
    --logo-navy: #17273a;
  }
  * { box-sizing: border-box; margin: 0; padding: 0; }
  html, body { width: 1200px; height: 960px; overflow: hidden; }
  body {
    background: var(--stage);
    font-family: "Lexend", sans-serif;
    color: var(--ink);
    position: relative;
  }
  .wrap {
    position: absolute;
    left: 45px; top: 90px;
    width: 1111px; height: 780px;
    display: flex;
  }
  .panel {
    position: relative;
    height: 100%;
    background: linear-gradient(180deg, var(--paper-top), var(--paper-bottom));
    overflow: hidden;
  }
  .back { width: 514px; }
  .spine { width: 83px; border-left: 1px solid #d8ccb8; border-right: 1px solid #d8ccb8; }
  .front { width: 514px; }

  /* back cover */
  .blurb {
    position: absolute; left: 130px; width: 268px;
    font-size: 9.4px; line-height: 16.2px; text-align: right;
  }
  .blurb-intro { top: 88px; }
  .blurb-bio { top: 410px; }
  .blurb-bio p + p { margin-top: 4px; }
  .back-title {
    position: absolute; left: 410px; top: 455px;
    transform: rotate(-90deg); transform-origin: 0 0;
    font-weight: 700; font-size: 22px; color: var(--title-blue);
    white-space: nowrap;
  }
  .author-portrait {
    position: absolute; left: 305px; top: 273px; width: 92px; height: 127px;
    background: radial-gradient(ellipse at 50% 35%, #2e94d6, var(--photo-blue) 60%, #145f91);
  }
  .back-author {
    position: absolute; right: 220px; top: 336px;
    font-weight: 300; font-size: 17px; color: #333; white-space: nowrap;
  }
  .publisher {
    position: absolute; left: 196px; top: 718px;
    display: flex; align-items: center; gap: 6px;
    font-weight: 700; font-size: 20px; color: var(--logo-navy);
  }
  .publisher .mark { width: 10px; height: 10px; background: var(--logo-navy); }
  .barcode-area {
    position: absolute; left: 367px; top: 697px; width: 140px; height: 78px;
    background: var(--barcode-box);
  }

  /* spine */
  .spine-title {
    position: absolute; left: 64px; top: 94px;
    transform: rotate(90deg); transform-origin: 0 0;
    font-weight: 700; font-size: 22px; color: var(--title-blue);
    white-space: nowrap;
  }
  .spine-author {
    position: absolute; left: 58px; top: 612px;
    transform: rotate(90deg); transform-origin: 0 0;
    font-weight: 300; font-size: 19px; color: #333; white-space: nowrap;
  }

  /* front cover */
  .skyline {
    position: absolute; left: 0; bottom: 0; width: 300px; height: 200px;
    background: linear-gradient(180deg, rgba(217,183,143,0) 0%, rgba(217,183,143,.55) 45%, var(--skyline) 100%);
  }
  .cover-photo {
    position: absolute; left: 266px; top: 240px; width: 248px; height: 540px;
    background: linear-gradient(180deg, rgba(230,210,185,0) 0%, rgba(122,63,42,.85) 35%, var(--jacket-brown) 100%);
    border-radius: 120px 120px 0 0;
  }
  .front-author {
    position: absolute; right: 16px; top: 48px;
    font-weight: 300; font-size: 27px; color: #222;
  }
  .cover-title {
    position: absolute; left: 24px; top: 96px;
    font-weight: 700; font-size: 68px; line-height: 70px;
    letter-spacing: -1.5px; color: var(--title-blue);
  }
  .cover-title span { display: block; }
  .rule { position: absolute; left: 28px; width: 186px; height: 1px; background: var(--rule-blue); }
  .rule-top { top: 526px; }
  .rule-bottom { top: 636px; }
  .tagline {
    position: absolute; left: 28px; top: 530px;
    font-weight: 300; font-size: 26px; line-height: 30px; color: #222;
  }
</style>
</head>
<body>
  <div class="wrap">
    <section class="panel back">
      <div class="blurb blurb-intro">
        What makes us unique in the legal field is we spent two years embedded in a large local immigration law firm with the ability to experiment and test campaigns, ads, and copy to get uncommon results. Soon law firms from Texas to California were requesting the same type of results we achieved right here in Millbrook. A year later, we've launched our own podcast introducing legal consumers to some of the top U.S. immigration attorneys. It's our way of giving back and using the relationships we've made to provide answers to people's most common questions about legal immigration.
      </div>
      <div class="author-portrait" role="img" aria-label="Author headshot on a blue backdrop"></div>
      <div class="back-author">Graham Ellery</div>
      <div class="back-title">A Studio Ledger Field Manual</div>
      <div class="blurb blurb-bio">
        <p>I have more than a decade of experience as a Senior Executive/Officer in billion-dollar Print Marketing and Direct Mail companies (including as Chief Marketing Officer).</p>
        <p>Since 2011, I've been the Founder and President of Summitway, LLC a Full-Service International award-winning Digital Marketing Agency serving clients primarily in the home services and legal fields.</p>
        <p>My perspective comes from working with both best-in-class Global 500 clients and entrepreneurs of niche small businesses. I am a former marketing mentor to startups associated with Forgeyard incubator and the Oakridge Economic Development corporation.</p>
      </div>
      <div class="publisher"><span class="mark"></span>Summitway</div>
      <div class="barcode-area"></div>
    </section>

    <section class="panel spine">
      <div class="spine-title">A Studio Ledger Field Manual</div>
      <div class="spine-author">Graham Ellery</div>
    </section>

    <section class="panel front">
      <div class="skyline" role="img" aria-label="Faded warm city skyline"></div>
      <div class="cover-photo" role="img" aria-label="Author in a brown plaid blazer, arms crossed"></div>
      <div class="front-author">Graham Ellery</div>
      <h1 class="cover-title">
        <span>A</span><span>Studio</span><span>Ledger</span><span>Field</span><span>Man</span><span>ual</span>
      </h1>
      <div class="rule rule-top"></div>
      <p class="tagline">Intake as a<br>Competitive<br>Advantage</p>
      <div class="rule rule-bottom"></div>
    </section>
  </div>
</body>
</html>
```